WordPress Site That Reviews Footwear

We need a wordpress web design for an affiliate site called PaceKite. We review and do roundups on footwear products. The final design should be clean and mobile friendly. The site should be built with Gutenberg page builder. We like the design of https://lunavessel.com/.
Updates

Need extra days to review

Target Market(s)

USA

Industry/Entity Type

Footwear

Northlane Text

PaceKite

Number of Pages Required

4 page

Font styles to use
Serif
Sans Serif

Requirements
Must have
• Wordpress site
Blog post
Page
Categories
Homepage

```html
<!DOCTYPE html>
<html lang="en">
<head>
<meta charset="utf-8">
<title>PaceKite — Footwear Reviews</title>
<link href="https://fonts.googleapis.com/css2?family=Roboto:ital,wght@0,400;0,500;0,700;1,400&display=swap" rel="stylesheet">
<style>
:root{
  --navy:#0d2f5a;
  --navy-deep:#0b2a52;
  --orange:#ef7a0c;
  --hero:#2a4a72;
  --text:#222;
  --muted:#666;
  --line:#e3e3e3;
  --soft:#f1f1f1;
  --white:#fff;
}
*{box-sizing:border-box;margin:0;padding:0}
html,body{width:1200px;height:2960px;overflow:hidden}
body{font-family:'Roboto',sans-serif;color:var(--text);background:var(--white);position:relative}
.abs{position:absolute}
section,header,footer{position:absolute;left:0;width:1200px;overflow:hidden}

/* header */
.site-header{top:0;height:76px;background:var(--white)}
.brand{left:114px;top:20px;font-size:30px;font-weight:700;color:#333}
.nav{top:32px;display:flex;gap:34px;font-size:16px;color:#333}
.site-header .nav{left:385px}
.btn-demo{left:918px;top:20px;width:169px;height:42px;border-radius:21px;background:var(--navy);color:var(--white);font-weight:500;font-size:15px;display:flex;align-items:center;justify-content:center}

/* hero */
.hero{top:76px;height:620px;background:linear-gradient(180deg,#2f4f78,#233f66)}
.hero-title{left:40px;top:166px;width:520px;text-align:center;color:var(--white);font-size:35px;font-weight:700;line-height:46px}
.hero-lede{left:60px;top:316px;width:480px;text-align:center;color:var(--white);font-size:16px;line-height:29px}
.btn{height:51px;border-radius:26px;display:flex;align-items:center;justify-content:center;font-size:16px;font-weight:500}
.btn-primary{left:86px;top:393px;width:154px;background:var(--orange);color:var(--white)}
.btn-ghost{left:250px;top:393px;width:247px;background:var(--white);color:#222}
.hero-shoe{left:540px;top:120px;width:470px;height:480px;border-radius:45% 55% 50% 40%;background:radial-gradient(ellipse at 40% 55%,#3b7be0,#2a4fb8 55%,rgba(42,74,114,0) 72%);transform:rotate(28deg)}
.quote-card{width:254px;height:138px;background:var(--white);border-radius:3px;padding:10px 12px}
.avatar{width:48px;height:48px;border-radius:50%;background:#c7b29a}
.qc-name{left:70px;top:16px;font-size:11px;font-weight:500;color:var(--navy)}
.qc-sub{left:70px;top:31px;font-size:9px;color:#777}
.qc-badge{right:10px;top:20px;width:38px;height:10px;border-radius:5px;background:#d6dce8}
.qc-text{left:17px;top:68px;width:225px;font-size:10px;font-style:italic;line-height:20px;color:#444}
.qc-mark{right:16px;bottom:10px;font-size:22px;color:#ccc;font-weight:700;line-height:1}
.dots{left:555px;top:587px;display:flex;gap:14px}
.dots i{width:12px;height:12px;border-radius:50%;background:rgba(255,255,255,.5)}
.dots i:first-child{background:var(--white)}

/* brand section */
.brand-sec{top:696px;height:829px;background:var(--white)}
.sec-title{width:1200px;text-align:center;font-size:40px;font-weight:700;color:var(--navy)}
.product-card{width:193px;height:267px;background:var(--white);box-shadow:0 1px 6px rgba(0,0,0,.18)}
.product-photo{width:193px;height:158px}
.pc-name{left:7px;top:175px;font-size:16px;font-weight:500}
.pc-price{left:7px;top:202px;font-size:16px;color:var(--orange)}
.pc-rate{left:7px;top:232px;font-size:11px;color:#333}
.stars{color:var(--orange);letter-spacing:-1px}
.review-panel{left:320px;top:166px;width:288px;height:578px;background:var(--white);box-shadow:0 1px 8px rgba(0,0,0,.18)}
.rp-head{left:29px;top:24px;font-size:13px;color:#333}
.rp-head b{color:#4a78d0;font-weight:400}
.rp-rule{left:16px;width:258px;height:1px;background:var(--line)}
.rp-copy{left:16px;top:72px;width:260px;font-size:13px;line-height:22px;color:#333}
.thumb{left:32px;width:54px;height:46px;box-shadow:0 0 3px rgba(0,0,0,.2)}
.rp-score{left:27px;top:396px;font-size:46px;color:var(--orange)}
.bar-row{left:126px;display:flex;align-items:center;gap:6px;font-size:11px;color:var(--navy)}
.bar{width:115px;height:5px;border-radius:3px;background:#ddd;position:relative}
.bar span{position:absolute;left:0;top:0;height:5px;border-radius:3px;background:var(--orange)}
.feature-h{left:633px;width:470px;font-size:31px;font-weight:500;line-height:38px;color:#222}
.feature-h em{font-style:normal;color:var(--orange)}
.feature-p{left:633px;width:480px;font-size:16px;line-height:28px;color:var(--muted)}

/* conversion */
.conv{top:1525px;height:557px;background:var(--soft)}
.conv-h{left:110px;top:140px;font-size:48px;font-weight:700;line-height:56px;color:#222}
.conv-h em{font-style:normal;color:var(--orange)}
.conv-p{left:111px;top:270px;width:480px;font-size:16px;line-height:28px;color:var(--muted)}
.rate-card{width:268px;background:var(--white);border-radius:16px;box-shadow:0 2px 10px rgba(0,0,0,.12)}
.ph{height:8px;background:#e2e2e2}
.rc-stars{font-size:17px;color:var(--orange);letter-spacing:2px}
.rc-text{font-size:12px;line-height:22px;color:#555}
.rc-row{display:flex;align-items:center;gap:10px;font-size:12px;color:var(--navy)}
.rc-row .bar{width:115px}

/* experts */
.experts{top:2082px;height:580px;background:var(--white)}
.expert-card{top:150px;width:318px;height:344px;background:var(--white);box-shadow:0 1px 6px rgba(0,0,0,.18);padding:26px 8px 0}
.expert-card p{font-size:14px;font-style:italic;line-height:26px;color:#555}
.source{right:18px;bottom:20px;font-size:24px;font-weight:700;color:#333}
.source.dot::before{content:"";display:inline-block;width:14px;height:14px;background:var(--orange);margin-right:6px;vertical-align:middle}
.arrow{top:300px}

/* partners */
.partners{top:2662px;height:128px;background:#f5f5f5}
.partner{top:46px;font-size:30px;font-weight:500;color:#333;display:flex;align-items:center;gap:10px}
.partner i{width:36px;height:36px;border-radius:50%;background:#333}

/* footer */
.site-footer{top:2790px;height:170px;background:var(--navy-deep)}
.site-footer .brand{top:42px;left:110px;font-size:48px;color:var(--white)}
.site-footer .nav{left:572px;top:68px;color:var(--white);gap:35px}
.social{left:111px;top:114px;display:flex;gap:10px}
.social i{width:14px;height:14px;border-radius:50%;background:var(--white)}
.copy{right:113px;top:114px;color:var(--white);font-size:16px}
</style>
</head>
<body>

<header class="site-header">
  <div class="abs brand">PaceKite</div>
  <nav class="abs nav"><span>Solutions</span><span>Pricing</span><span>Resources</span><span>Why Choose Us</span><span>Write Review</span></nav>
  <div class="abs btn-demo">Schedule a Demo</div>
</header>

<section class="hero">
  <div class="abs hero-shoe" role="img" aria-label="Blue running shoe photograph"></div>
  <h1 class="abs hero-title">Turn More Visitors into Active, Loyal Buyers with Product Ratings &amp; Reviews</h1>
  <p class="abs hero-lede">Lorem ipsum dolor sit amet, consectetur adipiscing elit, sed do eiusmod tempor incididunt ut labore et dolore</p>
  <div class="abs btn btn-primary">Get Started</div>
  <div class="abs btn btn-ghost">Watch Product Review Video</div>

  <div class="abs quote-card" style="left:779px;top:70px">
    <div class="abs avatar" style="left:12px;top:10px" role="img" aria-label="Reviewer portrait"></div>
    <div class="abs qc-name">Dana Whitfield</div>
    <div class="abs qc-sub">Lorem ipsum dolor sit amet</div>
    <div class="abs qc-badge" role="img" aria-label="Review platform badge"></div>
    <p class="abs qc-text">Lorem ipsum dolor sit amet, adipiscing elit, sed do eiusmod incididunt ut labore et dolore magna aliqua. Ut enim ad minim</p>
    <div class="abs qc-mark">”</div>
  </div>
  <div class="abs quote-card" style="left:891px;top:226px">
    <div class="abs avatar" style="left:12px;top:10px" role="img" aria-label="Reviewer portrait"></div>
    <div class="abs qc-name">Dana Whitfield</div>
    <div class="abs qc-sub">Lorem ipsum dolor sit amet</div>
    <div class="abs qc-badge" role="img" aria-label="Review platform badge"></div>
    <p class="abs qc-text">Lorem ipsum dolor sit amet, adipiscing elit, sed do eiusmod incididunt ut labore et dolore magna aliqua. Ut enim ad minim</p>
    <div class="abs qc-mark">”</div>
  </div>
  <div class="abs dots"><i></i><i></i><i></i><i></i></div>
</section>

<section class="brand-sec">
  <svg class="abs" style="left:0;top:0" width="600" height="600" viewBox="0 0 600 600" aria-hidden="true"><path d="M0 600 L0 0 L520 0 C560 160 540 360 420 470 C320 560 160 590 0 600Z" fill="#f3f3f3"/></svg>
  <h2 class="abs sec-title" style="top:76px">Build Your Brand</h2>

  <div class="abs product-card" style="left:111px;top:184px">
    <div class="product-photo" role="img" aria-label="Trail runner's shoes on rocky path" style="background:linear-gradient(135deg,#8a7a62,#4b4a3c)"></div>
    <div class="abs pc-name">Lorem ipsum dolor sit</div>
    <div class="abs pc-price">$20.00</div>
    <div class="abs pc-rate"><span class="stars">★★★★★</span> (150) Reviews</div>
  </div>
  <div class="abs product-card" style="left:111px;top:465px">
    <div class="product-photo" role="img" aria-label="Colourful strappy high heels" style="background:linear-gradient(135deg,#7a5a6a,#c2506a 50%,#5a7a4a)"></div>
    <div class="abs pc-name">Lorem ipsum dolor sit</div>
    <div class="abs pc-price">$20.00</div>
    <div class="abs pc-rate"><span class="stars">★★★★★</span> (150) Reviews</div>
  </div>

  <div class="abs review-panel">
    <div class="abs rp-head"><b>Revora</b> Reviews</div>
    <div class="abs rp-rule" style="top:52px"></div>
    <p class="abs rp-copy">Lorem ipsum dolor sit amet, consectetur adipiscing elit,</p>
    <div class="abs pc-rate" style="left:16px;top:124px"><span class="stars">★★★★★</span>(150) Reviews</div>
    <div class="abs thumb" style="top:166px;background:linear-gradient(135deg,#f4f4f4,#8a2a2a)" role="img" aria-label="Red sneaker thumbnail"></div>
    <div class="abs thumb" style="top:219px;background:linear-gradient(135deg,#f4d4d4,#d81a2a)" role="img" aria-label="Red heels thumbnail"></div>
    <div class="abs thumb" style="top:272px;background:linear-gradient(135deg,#f4f4f4,#222)" role="img" aria-label="Black sneaker thumbnail"></div>
    <div class="abs" style="left:115px;top:154px;width:148px;height:178px;background:linear-gradient(180deg,#5b7fa8,#5a7290 55%,#7a4e32)" role="img" aria-label="Brown leather boots with jeans"></div>
    <div class="abs rp-rule" style="top:354px"></div>
    <div class="abs" style="left:16px;top:368px;font-size:13px;color:#333">Reviews</div>
    <div class="abs rp-score">4.8</div>
    <div class="abs" style="left:31px;top:450px;font-size:11px;color:#888">★★★★★</div>
    <div class="abs bar-row" style="top:377px">5 Star<div class="bar"><span style="width:85%"></span></div></div>
    <div class="abs bar-row" style="top:398px">4 Star<div class="bar"><span style="width:10%"></span></div></div>
    <div class="abs bar-row" style="top:420px">3 Star<div class="bar"><span style="width:25%"></span></div></div>
    <div class="abs bar-row" style="top:441px">2 Star<div class="bar"><span style="width:33%"></span></div></div>
    <div class="abs bar-row" style="top:463px">1 Star<div class="bar"><span style="width:18%"></span></div></div>
    <p class="abs" style="left:15px;top:496px;width:265px;font-size:12px;line-height:21px;color:#444">Lorem ipsum dolor sit amet, adipiscing elit, sed do eiusmod tempor incididunt ut labore et dolore magna aliqua. Ut enim ad minim veniam, quis</p>
  </div>

  <h3 class="abs feature-h" style="top:192px">Creates INSTANT Brand Trust and <em>Product Credibility</em></h3>
  <p class="abs feature-p" style="top:288px">Lorem ipsum dolor sit amet, consectetur adipiscing elit, sed do eiusmod tempor incididunt ut labore et dolore magna aliqua. Ut enim ad minim veniam, quis nostrud exercitation ullamco laboris nisi ut aliquip ex ea commodo consequat. Duis aute irure dolor in reprehenderit in voluptate velit esse cillum dolore</p>
  <h3 class="abs feature-h" style="top:466px">Lorem ipsum dolor sit amet, consectetur adipiscing elit,</h3>
  <p class="abs feature-p" style="top:562px">Lorem ipsum dolor sit amet, consectetur adipiscing elit, sed do eiusmod tempor incididunt ut labore et dolore magna aliqua. Ut enim ad minim veniam, quis nostrud exercitation ullamco laboris nisi ut aliquip ex ea commodo consequat. Duis aute irure dolor in reprehenderit in voluptate velit esse cillum dolore</p>
</section>

<section class="conv">
  <div class="abs" style="left:660px;top:40px;width:440px;height:440px;border-radius:50%;background:#e9e9e9"></div>
  <h2 class="abs conv-h">Increases Your<br><em>Conversion Rate</em></h2>
  <p class="abs conv-p">Lorem ipsum dolor sit amet, consectetur adipiscing elit, sed do eiusmod tempor incididunt ut labore et dolore magna aliqua. Ut enim ad minim veniam, quis nostrud exercitation ullamco laboris nisi ut aliquip ex ea commodo consequat. Duis aute irure dolor in reprehenderit in voluptate velit esse cillum dolore</p>

  <div class="abs rate-card" style="left:805px;top:30px;height:353px">
    <div class="abs ph" style="left:97px;top:28px;width:143px"></div>
    <div class="abs ph" style="left:97px;top:44px;width:56px"></div>
    <div class="abs rc-stars" style="left:10px;top:134px">★★★★★</div>
    <p class="abs rc-text" style="left:62px;top:180px;width:200px">um dolor sit amet, adipiscing elit, sed od tempor incididunt ut dolore magna enim ad minim veniam,</p>
    <div class="abs rc-row" style="left:80px;top:240px"><div class="bar"><span style="width:85%"></span></div>5/5</div>
    <div class="abs rc-row" style="left:60px;top:264px">ty <div class="bar"><span style="width:85%"></span></div>5/5</div>
  </div>
  <div class="abs" style="left:760px;top:22px;width:170px;height:100px;border-radius:40% 50% 40% 30%;background:linear-gradient(135deg,#333,#111)" role="img" aria-label="Pair of black sneakers"></div>

  <div class="abs rate-card" style="left:600px;top:185px;height:352px">
    <div class="abs ph" style="left:96px;top:28px;width:142px"></div>
    <div class="abs ph" style="left:96px;top:44px;width:56px"></div>
    <div class="abs rc-stars" style="left:8px;top:130px">★★★★★</div>
    <p class="abs rc-text" style="left:8px;top:175px;width:252px">Lorem ipsum dolor sit amet, adipiscing elit, sed do eiusmod tempor incididunt ut dolore magna aliqua. Ut enim ad minim veniam,</p>
    <div class="abs rc-row" style="left:33px;top:255px">Price <div class="bar"><span style="width:85%"></span></div>5/5</div>
    <div class="abs rc-row" style="left:33px;top:279px">Quality <div class="bar"><span style="width:85%"></span></div>5/5</div>
  </div>
  <div class="abs" style="left:560px;top:155px;width:125px;height:150px;border-radius:40%;background:linear-gradient(135deg,#8a6a4a,#3a3a3a)" role="img" aria-label="Pair of brown leather slides"></div>
</section>

<section class="experts">
  <h2 class="abs sec-title" style="top:76px;font-size:37px">Here’s what the Experts Say about <span style="color:var(--orange)">Product Reviews</span></h2>
  <svg class="abs arrow" style="left:82px" width="16" height="28" viewBox="0 0 16 28" aria-hidden="true"><path d="M13 3 3 14l10 11" stroke="#333" stroke-width="2.5" fill="none"/></svg>
  <svg class="abs arrow" style="left:1100px" width="16" height="28" viewBox="0 0 16 28" aria-hidden="true"><path d="M3 3l10 11L3 25" stroke="#333" stroke-width="2.5" fill="none"/></svg>

  <div class="abs expert-card" style="left:111px">
    <p>Lorem ipsum dolor sit amet, consectetur adipiscing elit, sed do eiusmod tempor incididunt ut labore et dolore magna aliqua. Ut enim ad minim veniam, quis nostrud exercitation ullamco laboris nisi ut aliquip ex ea commodo consequat. Duis aute irure dolor in reprehenderit in voluptate velit esse cillum dolore eu fugiat nulla pariatur. Excepteur sint occaecat cupidatat non proident, sunt in culpa qui officia deserunt mollit anim id est laborum &nbsp;”</p>
    <div class="abs source">Revora</div>
  </div>
  <div class="abs expert-card" style="left:441px">
    <p>Lorem ipsum dolor sit amet, consectetur adipiscing elit, sed do eiusmod tempor incididunt ut labore et dolore magna aliqua. Ut enim ad minim veniam, quis nostrud exercitation ullamco laboris nisi ut aliquip ex ea commodo consequat. Duis aute irure dolor in reprehenderit in voluptate velit esse cillum dolore eu fugiat nulla pariatur. Excepteur sint occaecat cupidatat non proident, sunt in culpa qui officia deserunt mollit anim id est laborum &nbsp;”</p>
    <div class="abs source dot">TrustNest</div>
  </div>
  <div class="abs expert-card" style="left:770px">
    <p>Lorem ipsum dolor sit amet, consectetur adipiscing elit, sed do eiusmod tempor incididunt ut labore et dolore magna aliqua. Ut enim ad minim veniam, quis nostrud exercitation ullamco laboris nisi ut aliquip ex ea commodo consequat. Duis aute irure dolor in reprehenderit in voluptate velit esse cillum dolore eu fugiat nulla pariatur. Excepteur sint occaecat cupidatat non proident, sunt in culpa qui officia deserunt mollit anim id est laborum &nbsp;”</p>
    <div class="abs source">Shopwell</div>
  </div>
</section>

<section class="partners">
  <div class="abs partner" style="left:113px"><i></i>Northlane</div>
  <div class="abs partner" style="left:292px">Fernhill</div>
  <div class="abs partner" style="left:510px">Corvex</div>
  <div class="abs partner" style="left:722px">Brightmark</div>
  <div class="abs partner" style="left:965px">Stridebox</div>
</section>

<footer class="site-footer">
  <div class="abs brand">PaceKite</div>
  <nav class="abs nav"><span>Solutions</span><span>Pricing</span><span>Resources</span><span>Why Choose Us</span><span>Write Review</span></nav>
  <div class="abs social" aria-label="Social links"><i></i><i></i><i></i></div>
  <div class="abs copy">© 2021 All Rights Reserved</div>
</footer>

</body>
</html>
```